female esthetician looking for an impact business card

I an an expert in skin care industry with high experience in NYC.I want my business card to look professional , an impact at first look. I do want a combination between white and gold . I believe the font will be great if is gold.. The Fonts are also important. MIRABELA COSTINA (SKIN CARE BOUTIQUE)

THIS SHOULD BE THE BUSINESS NAME, and should be placed on th eback of the card.
IN front m, the name MIRABELA COSTINA - ESTHETCIAN

BY APPOINTMENTS ONLY: 518.240.7136

Target Market(s)

HIGH END CLIENTELE

Contact Information for Business Card

iT WILL BE on a luxury paper. I neeed the wow feeling

Requirements
Should not have
• pictures

```html
<!DOCTYPE html>
<html lang="en">
<head>
<meta charset="utf-8">
<title>Mirabela Costina – Business Card</title>
<link href="https://fonts.googleapis.com/css2?family=Arvo:wght@400;700&family=Lato:wght@400;700&display=swap" rel="stylesheet">
<style>
  :root {
    --backdrop: #2b2b2d;
    --card: #1f1f21;
    --gold: #f2b835;
    --gold-light: #f7cf4a;
    --white: #f4f4f4;
    --rule: #6c6c6c;
    --pattern: #2a2a2c;
  }
  * { box-sizing: border-box; margin: 0; padding: 0; }
  html, body { width: 1200px; height: 1108px; overflow: hidden; background: var(--backdrop); }
  .canvas {
    width: 1200px; height: 1108px; position: relative;
    display: flex; justify-content: center; align-items: center; gap: 70px;
  }
  .card {
    width: 420px; height: 700px; border-radius: 22px;
    background: var(--card); position: relative; overflow: hidden;
    box-shadow: 0 14px 30px rgba(0,0,0,.45);
  }
  /* front */
  .card-front { display: flex; flex-direction: column; align-items: center; padding-top: 78px; text-align: center; }
  .brand-mark { width: 96px; height: 96px; border-radius: 50%; background: var(--gold); margin-bottom: 38px; }
  .brand-name {
    font-family: "Arvo", serif; font-weight: 400; font-size: 31px; letter-spacing: 1px;
    color: var(--gold-light); line-height: 1; white-space: nowrap;
  }
  .brand-tagline {
    font-family: "Arvo", serif; font-size: 22px; color: var(--white); margin-top: 8px;
  }
  .person-name {
    font-family: "Lato", sans-serif; font-weight: 700; font-size: 31px; color: var(--gold-light);
    margin-top: 46px; letter-spacing: .5px; line-height: 1;
  }
  .person-role { font-family: "Lato", sans-serif; font-size: 19px; color: var(--white); margin-top: 4px; }
  .icon-rule { display: flex; align-items: center; width: 250px; margin-top: 18px; gap: 6px; }
  .icon-rule .line { flex: 1; height: 1px; background: var(--rule); }
  .icon-rule svg { width: 24px; height: 24px; display: block; }
  .contact-list { list-style: none; font-family: "Lato", sans-serif; font-size: 20px; color: var(--white); margin-top: 14px; line-height: 1.35; }
  .contact-divider { width: 250px; height: 1px; background: var(--rule); margin: 14px 0 12px; }
  .address { font-family: "Lato", sans-serif; font-size: 20px; color: var(--white); line-height: 1.35; font-style: normal; }
  /* back */
  .card-back .pattern-field {
    position: absolute; inset: 0 0 200px 0;
    background: linear-gradient(170deg, var(--pattern) 0%, var(--card) 100%);
  }
  .card-back .back-title {
    position: absolute; left: 0; right: 0; bottom: 86px; text-align: center;
  }
  .card-back .brand-name { color: var(--white); }
</style>
</head>
<body>
<main class="canvas">
  <section class="card card-front" aria-label="Card front">
    <div class="brand-mark" aria-hidden="true"></div>
    <h1 class="brand-name">MIRABELA COSTINA</h1>
    <p class="brand-tagline">skin care expert</p>
    <h2 class="person-name">DANIEL MERCER</h2>
    <p class="person-role">Managing Director</p>
    <div class="icon-rule">
      <span class="line"></span>
      <svg viewBox="0 0 24 24" aria-label="phone"><circle cx="12" cy="12" r="12" fill="#f2b835"/><path d="M8 6.5l2 .2.9 2.6-1.3 1a7 7 0 003.1 3.1l1-1.3 2.6.9.2 2c-.9.9-2 1.2-3.2.8A10 10 0 017.2 9.7c-.4-1.2-.1-2.3.8-3.2z" fill="#1f1f21"/></svg>
      <svg viewBox="0 0 24 24" aria-label="email"><circle cx="12" cy="12" r="12" fill="#f2b835"/><rect x="6" y="8" width="12" height="8.5" fill="none" stroke="#1f1f21" stroke-width="1.5"/><path d="M6 8l6 5 6-5" fill="none" stroke="#1f1f21" stroke-width="1.5"/></svg>
      <svg viewBox="0 0 24 24" aria-label="website"><circle cx="12" cy="12" r="12" fill="#f2b835"/><circle cx="12" cy="12" r="6.5" fill="none" stroke="#1f1f21" stroke-width="1.4"/><ellipse cx="12" cy="12" rx="2.8" ry="6.5" fill="none" stroke="#1f1f21" stroke-width="1.2"/><path d="M5.5 12h13" stroke="#1f1f21" stroke-width="1.2"/></svg>
      <span class="line"></span>
    </div>
    <ul class="contact-list">
      <li>518.240.7136</li>
      <li>hello@mirabelaskin.com</li>
      <li>www.mirabelaskin.com</li>
    </ul>
    <div class="contact-divider"></div>
    <address class="address">218 Lexington Ave, Suite 4,<br>New York, NY 10016</address>
  </section>

  <section class="card card-back" aria-label="Card back">
    <div class="pattern-field" role="img" aria-label="Faint repeating brand pattern"></div>
    <div class="back-title">
      <h1 class="brand-name">MIRABELA COSTINA</h1>
      <p class="brand-tagline">skin care expert</p>
    </div>
  </section>
</main>
</body>
</html>
```